HOT TUB - SPAS service needs an business card

I need an business for my company who his specialise in a maintenance,water treatment and cleaning of Hot Tub - Spas for commercial and residential customers. The company operate mainly in the ski resort of Chamonix, Megève and St Gervais. The final product should communicate pure water, cleanest and professional for luxury property's.
I have upload a logo but any improvement on it is welcome.(color,size, details etc..) or any other idea. Thank you
Company Name: 58 BAINS
My name: Lucien Marchetti
Email: lucimarch@examplemail.net
Tel: +33 (0)6 71 58 29 64
Description to be on the card in french(first langage) and in English:
- Spas service
- Entretien, traitement eau, nettoyage.
- Maintenance, water treatment, cleaning.
Industry/Entity Type
Residential
Colors
Designer to choose colors to be used in the design.
Look and feel
Each slider illustrates characteristics of the customer's brand and the style your logo design should communicate.

```html
<!DOCTYPE html>
<html lang="fr">
<head>
<meta charset="utf-8">
<title>58 BAINS – carte de visite</title>
<link rel="stylesheet" href="https://fonts.googleapis.com/css2?family=Source+Sans+3:wght@400;700&display=swap">
<style>
  :root {
    --bg: #ecebe8;
    --sky: #22a7fd;
    --rule: #9bdafd;
    --deep: #0b63d1;
    --white: #ffffff;
  }
  * { box-sizing: border-box; margin: 0; padding: 0; }
  html, body { width: 1200px; height: 1100px; overflow: hidden; }
  body {
    background: var(--bg);
    position: relative;
    font-family: "Source Sans 3", "Myriad Pro", Arial, sans-serif;
    color: var(--white);
  }
  .card {
    position: absolute;
    width: 870px;
    height: 497px;
    background: var(--sky);
    overflow: hidden;
    box-shadow: 0 2px 6px rgba(0,0,0,0.18);
  }
  .card--front { left: 316px; top: 38px; }
  .card--back { left: 52px; top: 583px; }

  .brand {
    position: absolute;
    left: 0; right: 0;
    display: flex;
    align-items: center;
    justify-content: center;
    gap: 18px;
    font-weight: 700;
    letter-spacing: 0.5px;
  }
  .brand__dot {
    width: 34px; height: 34px;
    border: 3px solid var(--white);
    border-radius: 50%;
  }
  .card--front .brand { top: 220px; font-size: 46px; }
  .card--back .brand { top: 190px; font-size: 46px; }

  .card__rule {
    position: absolute;
    left: 0; right: 0;
    top: 344px; height: 5px;
    background: var(--rule);
  }
  .contact-band {
    position: absolute;
    left: 0; right: 0;
    top: 352px; bottom: 0;
    background: var(--deep);
  }
  .contact-band__name {
    position: absolute;
    right: 508px;
    top: 54px;
    font-size: 31px;
    font-weight: 700;
    white-space: nowrap;
  }
  .contact-band__divider {
    position: absolute;
    left: 392px;
    top: 33px;
    width: 1px; height: 79px;
    background: rgba(255,255,255,0.55);
  }
  .contact-list {
    position: absolute;
    left: 418px;
    top: 34px;
    list-style: none;
    font-size: 30px;
    line-height: 45px;
  }
  .contact-list li { display: flex; align-items: center; gap: 10px; white-space: nowrap; }
  .contact-list svg { width: 26px; height: 26px; flex: none; }
  .contact-list .phone { font-weight: 700; }

  .services {
    position: absolute;
    left: 0; right: 0;
    top: 343px;
    text-align: center;
  }
  .services__title {
    font-size: 31px;
    font-weight: 700;
    margin-left: -4px;
    line-height: 42px;
  }
  .services__list {
    font-size: 31px;
    line-height: 42px;
    margin-top: 7px;
    word-spacing: 1px;
  }
</style>
</head>
<body>

<section class="card card--front" aria-label="Recto de la carte">
  <div class="brand"><span class="brand__dot"></span><span class="brand__name">58 BAINS</span></div>
  <div class="card__rule"></div>
  <div class="contact-band">
    <p class="contact-band__name">Lucien Marchetti</p>
    <div class="contact-band__divider"></div>
    <ul class="contact-list">
      <li class="phone">
        <svg viewBox="0 0 26 26" aria-hidden="true"><circle cx="13" cy="13" r="11" fill="none" stroke="#fff" stroke-width="2"/><path d="M9 7c-1 1-1 3 0 5 1 3 3 5 6 6 2 1 3 0 4-1l-2-2-2 1c-2-1-3-2-4-4l1-2z" fill="#fff"/></svg>
        <span>+33 (0)6 71 58 29 64</span>
      </li>
      <li class="email">
        <svg viewBox="0 0 26 26" aria-hidden="true"><path d="M2 11 13 4l11 7v11H2z" fill="#fff"/><path d="M2 11l11 7 11-7" fill="none" stroke="#0b63d1" stroke-width="2"/></svg>
        <span>lucimarch@examplemail.net</span>
      </li>
    </ul>
  </div>
</section>

<section class="card card--back" aria-label="Verso de la carte">
  <div class="brand"><span class="brand__dot"></span><span class="brand__name">58 BAINS</span></div>
  <div class="services">
    <h2 class="services__title">SPAS SERVICES</h2>
    <p class="services__list">• Entretien • traitement eau • nettoyage<br>• Maintenance • water treatment • cleaning.</p>
  </div>
</section>

</body>
</html>
```